Sell the dream! Property investment proposal document

We are looking for a proposal document which outlines our vision for property development. The purpose of the document is to raise investment from investors - sell the dream!
Brief summary:
Kestrel Dwellings Developments, is an emerging New Zealand property investment company with a focus on providing unique property investment opportunities.
Our expertise and capabilities in architectural modular homes provide us with a remarkable advantage in tackling the development of properties that are typically considered challenging, remote, or uniquely positioned.
Our specialization in this niche sector of property development not only sets us apart from competitors, but also paves the way for lucrative investment opportunities in the New Zealand property market.
Feel free to use any images from www.kestreldwellings.co.nz
Target Market(s)
investors for a unique property development opportunity
Industry/Entity Type
luxury property development in unique locations throughout New Zealand
Colors
Designer to choose only greyscale colors for use in the design.
Look and feel

```html
<!DOCTYPE html>
<html lang="en">
<head>
<meta charset="utf-8">
<title>Kestrel Dwellings Developments – Investment Proposal</title>
<link href="https://fonts.googleapis.com/css2?family=Poppins:wght@300;400;600;700&display=swap" rel="stylesheet">
<style>
:root{
  --stage:#dedede;
  --page:#1f1f1f;
  --page-dark:#1b1b1b;
  --panel:#232323;
  --band:#2e2e2e;
  --ink:#ffffff;
  --ink-soft:#d6d6d6;
  --ink-mute:#8a8a8a;
  --tag:#4a4a4a;
}
*{margin:0;padding:0;box-sizing:border-box}
html,body{width:1034px;height:1200px;overflow:hidden;background:var(--stage)}
body{font-family:'Poppins',sans-serif;color:var(--ink);position:relative}
.spread{position:absolute;left:51px;width:933px;height:329px;background:var(--page);overflow:hidden;box-shadow:0 6px 14px rgba(0,0,0,.35)}
.spread--cover{top:71px;width:935px}
.spread--overview{top:434px}
.spread--finance{top:795px}
.abs{position:absolute}
.texture{background:var(--page-dark)}
.photo{position:absolute}
.photo--framed{border:2px solid #4a4a4a}
.brand{position:absolute;font-weight:400;letter-spacing:-.5px;line-height:1;color:var(--ink)}
.contact{position:absolute;left:49px;top:237px;font-size:6.5px;line-height:10.5px;color:var(--ink-soft)}
.contact li{list-style:none;display:flex;align-items:center;gap:6px}
.contact svg{width:7px;height:7px}
.hero-sell{position:absolute;left:692px;top:146px;font-size:29px;font-weight:300;color:#9a9a9a;line-height:1}
.hero-dream{position:absolute;left:692px;top:168px;font-size:29px;font-weight:700;line-height:1;letter-spacing:.3px}
.hero-sub{position:absolute;left:692px;top:201px;font-size:8px;font-weight:300;line-height:10.5px;color:var(--ink-soft)}
.hero-url{position:absolute;left:692px;top:271px;font-size:7.5px;letter-spacing:2.2px;color:var(--ink-soft)}
.hero-url b{font-weight:700;color:var(--ink)}
.heading{position:absolute;font-size:10px;letter-spacing:3px;font-weight:400;white-space:nowrap}
.heading span{color:var(--ink-mute);font-weight:600}
.body{position:absolute;font-size:4.4px;line-height:5.9px;color:var(--ink-soft);font-weight:300}
.body p{margin-bottom:5.6px}
.footer-url{position:absolute;font-size:6px;letter-spacing:1.2px;color:var(--ink-soft);display:flex;align-items:center;gap:7px}
.footer-url i{font-style:normal;background:var(--tag);font-size:5.5px;padding:0 3px;letter-spacing:0}
</style>
</head>
<body>

<!-- Cover spread -->
<section class="spread spread--cover">
  <div class="photo" role="img" aria-label="Dark, dimmed photograph of a modern low-roofed home on a grassy hillside" style="left:0;top:0;width:935px;height:330px;background:linear-gradient(180deg,#262626 0%,#222 45%,#1e1e1e 100%)"></div>
  <div class="abs texture" role="img" aria-label="Subtle dark leaf pattern panel" style="left:342px;top:0;width:251px;height:330px;background:#1c1c1c"></div>
  <div class="brand" style="left:49px;top:193px;font-size:36px">Kestrel</div>
  <ul class="contact">
    <li><svg viewBox="0 0 10 10"><path d="M2 1l2 2-1 1.5c.8 1.5 1.7 2.4 3 3L7.5 6l2 2-1.5 1.5C4.5 9 1 5.5.5 2.5z" fill="#9a9a9a"/></svg>09 555 0142</li>
    <li><svg viewBox="0 0 10 10"><rect x="1" y="2" width="8" height="6" fill="#9a9a9a"/><path d="M1 2l4 3 4-3" stroke="#222" fill="none"/></svg>sales@kestreldwellings.co.nz</li>
    <li><svg viewBox="0 0 10 10"><circle cx="5" cy="5" r="4" stroke="#9a9a9a" fill="none"/><path d="M1 5h8M5 1c-2 2.5-2 5.5 0 8M5 1c2 2.5 2 5.5 0 8" stroke="#9a9a9a" fill="none" stroke-width=".7"/></svg>www.kestreldwellings.co.nz</li>
  </ul>
  <div class="brand" style="left:690px;top:66px;font-size:50px">Kestrel</div>
  <div class="hero-sell">SELL</div>
  <div class="hero-dream">THE DREAM!</div>
  <div class="hero-sub">Homes Developments, is an emerging<br>New Zealand property investment company</div>
  <div class="hero-url">www.<b>kestreldwellings</b>.co.nz</div>
</section>

<!-- Overview / Origins spread -->
<section class="spread spread--overview">
  <div class="heading" style="left:49px;top:49px">BUSINESS <span>OVERVIEW</span></div>
  <div class="body" style="left:49px;top:75px;width:142px">
    <p>Kestrel Dwellings Developments, is an emerging New Zealand property investment company with a focus on providing unique property investment opportunities.</p>
    <p>Our expertise and capabilities in architectural modular homes provide us with a remarkable advantage in tackling the development of properties that are typically considered challenging, remote, or uniquely positioned.</p>
    <p>As a company, with 48 employees boasting a wealth of experience in handling complex architectural projects, making us well-equipped to navigate the intricacies and demands of such ventures.</p>
    <p>This advantage allows us to not only execute projects efficiently but also to deliver exceptional results within condensed time frames.</p>
    <p>By capitalizing on our ability to develop difficult, remote, or one-of-a-kind properties swiftly and effectively, Kestrel Dwellings Developments offers investors a rare chance to engage in projects that promise exceptional profitability in the New Zealand property market.</p>
    <p>Our specialization in this niche sector of property development not only sets us apart from competitors, but also paves the way for lucrative investment opportunities in the New Zealand property market.</p>
  </div>
  <div class="brand" style="left:49px;top:258px;font-size:17px">Kestrel</div>
  <div class="photo" role="img" aria-label="Glass pavilion home on a pebbled coastline at sunset" style="left:254px;top:0;width:212px;height:257px;background:linear-gradient(180deg,#b9c3cc 0%,#d9cfae 45%,#6f6e68 62%,#5a5148 100%)"></div>
  <div class="abs" style="left:254px;top:257px;width:212px;height:72px;background:var(--band)"></div>
  <div class="footer-url" style="left:286px;top:271px">www.kestreldwellings.co.nz <i>01</i></div>

  <div class="abs texture" role="img" aria-label="Subtle dark leaf pattern panel" style="left:713px;top:0;width:220px;height:329px"></div>
  <div class="heading" style="left:517px;top:49px">BUSINESS <span>ORIGINS</span></div>
  <div class="body" style="left:517px;top:75px;width:160px">
    <p>Kestrel Dwellings Developments, is an emerging New Zealand property investment company with a focus on providing unique property investment opportunities.</p>
    <p>Our expertise and capabilities in architectural modular homes provide us with a remarkable advantage in tackling the development of properties that are typically considered challenging, remote, or uniquely positioned.</p>
    <p>As a company, with 48 employees boasting a wealth of experience in handling complex architectural projects, making us well-equipped to navigate the intricacies and demands of such ventures.</p>
    <p>This advantage allows us to not only execute projects efficiently but also to deliver exceptional results within condensed time frames.</p>
    <p>By capitalizing on our ability to develop difficult, remote, or one-of-a-kind properties swiftly and effectively, Kestrel Dwellings Developments offers investors a rare chance to engage in projects that promise exceptional profitability in the New Zealand property market.</p>
    <p>Our specialization in this niche sector of property development not only sets us apart from competitors, but also paves the way for lucrative investment opportunities in the New Zealand property market.</p>
  </div>
  <div class="brand" style="left:514px;top:258px;font-size:17px">Kestrel</div>
  <div class="photo photo--framed" role="img" aria-label="Living room with lounge chair looking through glass onto the ocean" style="left:739px;top:41px;width:144px;height:96px;background:linear-gradient(180deg,#8fb8e0 0%,#4d7fa8 55%,#2a2a2a 75%,#1a1a1a 100%)"></div>
  <div class="photo photo--framed" role="img" aria-label="Bright interior with wide windows over green hills and a harbour" style="left:739px;top:150px;width:144px;height:96px;background:linear-gradient(180deg,#eae6df 0%,#9dbbd4 30%,#6f8f4f 60%,#c7a27a 100%)"></div>
  <div class="footer-url" style="left:752px;top:271px">www.kestreldwellings.co.nz <i>01</i></div>
</section>

<!-- Advantage / Finance spread -->
<section class="spread spread--finance">
  <div class="abs texture" role="img" aria-label="Subtle dark leaf pattern band" style="left:100px;top:0;width:248px;height:40px"></div>
  <div class="photo photo--framed" role="img" aria-label="Dark timber modular home on rolling coastal farmland at dusk" style="left:51px;top:48px;width:366px;height:111px;background:linear-gradient(180deg,#8f8c80 0%,#55573a 40%,#4c4d28 70%,#3a3a22 100%);border-width:1px"></div>
  <div class="heading" style="left:49px;top:181px">COMPETITIVE <span>ADVANTAGE</span></div>
  <div class="body" style="left:49px;top:200px;width:372px">
    <p>Our competitive advantage lies in the uniqueness of our property investment opportunities. Unlike traditional real estate companies, we focus on offering properties that are not only profitable but also aesthetically pleasing and unique. By catering to the tastes of architecture lovers, we set ourselves apart from the competition and attract a niche market of customers who appreciate the artistry and design of our projects.</p>
    <p>Additionally, the streamlined and condensed timelines facilitated by our modular approach provide quicker returns on investment.</p>
  </div>
  <div class="brand" style="left:49px;top:258px;font-size:17px">Kestrel</div>
  <div class="footer-url" style="left:286px;top:271px">www.kestreldwellings.co.nz <i>01</i></div>

  <div class="abs texture" role="img" aria-label="Subtle dark leaf pattern panel" style="left:713px;top:0;width:220px;height:329px"></div>
  <div class="heading" style="left:517px;top:49px">FINANCIAL <span>SUMMARY</span></div>
  <div class="body" style="left:517px;top:74px;width:152px">
    <p>In terms of financial projections, with each development, we anticipate a profit of 10%-20% which will be project dependent.</p>
    <p>This growth is fueled by the increasing demand for unique property investments in New Zealand and our ability to deliver high-quality services to the market in a condensed time frame, with heavily controlled costs.</p>
    <p>With a solid business model and a dedicated team, we are confident in our ability to achieve success and establish Kestrel Dwellings Investments as a trusted name in the industry.</p>
    <p>New Zealand's property market has been experiencing steady growth over the years, making it an attractive destination for property investors. With its beautiful landscapes and strong economy, New Zealand offers a diverse range of investment opportunities for both local and international investors. The demand for quality properties in prime locations continues to rise, creating a favorable environment for property investment companies like ours that can lean on our modular benefits of being able to reach unique and remote locations.</p>
  </div>
  <div class="brand" style="left:514px;top:258px;font-size:17px">Kestrel</div>
  <div class="photo photo--framed" role="img" aria-label="Corner glass room with armchair overlooking misty mountains" style="left:739px;top:41px;width:144px;height:211px;background:linear-gradient(180deg,#3b342d 0%,#9a9c98 25%,#8a7a62 55%,#4a4642 80%,#2c2a28 100%)"></div>
  <div class="footer-url" style="left:752px;top:271px">www.kestreldwellings.co.nz <i>01</i></div>
</section>

</body>
</html>
```